New Business Card for our Indoor Golf Training Facility

We are looking for designs for a new business card for our indoor golf training facility. Attached is our logo, our logo with our slogan, and here is our elevator pitch (What makes us different from the others) not sure if all the info will fit on one card, maybe you can condense the elevator pitch? here is the info

Elevator Pitch
We work with serious golfers and those that want to be serious golfers…
to make you better, faster, at all phases of the game…
We use the same state-of-the-art technology as professional golfers…
which produces data sets that shows your improvement in real time.
Our facility is available 24/7 to our members, which allows you to improve on your time.

our website: www.birchpinlinks.com

Target Market(s)

Golfers

Font styles to use
Serif
Sans Serif

Colors
ec1f27
f59195
fbd4d5
919191
d3d3d3
1b1b1b

Requirements
Must have
• our logo or our logo with the slogan, elevator pitch (can be condensed or shortened)

```html
<!DOCTYPE html>
<html lang="en">
<head>
<meta charset="utf-8">
<title>Birch Pin Links – Business Card</title>
<link href="https://fonts.googleapis.com/css2?family=Work+Sans:wght@400;500;600&family=Roboto:wght@400&display=swap" rel="stylesheet">
<style>
  :root {
    --backdrop: #232323;
    --card: #161616;
    --card-edge: #202020;
    --emboss: #0c0c0c;
    --silver: #d3d3d3;
    --grey: #919191;
    --rule: #5a5a5a;
  }
  * { margin: 0; padding: 0; box-sizing: border-box; }
  html, body { width: 1200px; height: 900px; overflow: hidden; }
  body {
    background: var(--backdrop);
    font-family: "Work Sans", sans-serif;
    position: relative;
  }
  .card {
    position: absolute;
    left: 260px;
    width: 680px;
    height: 390px;
    background: var(--card);
    border: 1px solid var(--card-edge);
  }
  .card--back { top: 45px; }
  .card--front { top: 465px; }

  .brand { display: flex; align-items: center; gap: 14px; }
  .brand__dot {
    width: 52px; height: 52px; border-radius: 50%;
    border: 3px solid currentColor; flex: none;
  }
  .brand__name { font-weight: 600; font-size: 46px; letter-spacing: 0.5px; line-height: 1; }
  .slogan { font-size: 14px; letter-spacing: 0.6px; margin-top: 4px; }

  /* back side */
  .card--back .brand-block { position: absolute; left: 150px; top: 60px; color: var(--silver); }
  .card--back .slogan { color: var(--silver); margin-left: 66px; }
  .pitch {
    position: absolute; left: 40px; right: 40px; top: 190px;
    font-family: "Roboto", sans-serif; text-align: center;
    font-size: 14px; line-height: 20px; color: var(--grey);
  }
  .pitch__title { font-size: 16px; color: var(--grey); margin-bottom: 4px; }

  /* front side */
  .card--front .brand-block { position: absolute; left: 40px; top: 140px; color: #2a2a2a; }
  .card--front .brand__name { font-size: 40px; }
  .card--front .brand__dot { width: 46px; height: 46px; }
  .card--front .slogan { color: #2a2a2a; margin-left: 60px; }
  .divider {
    position: absolute; left: 395px; top: 60px; width: 1px; height: 270px;
    background: var(--rule);
  }
  .contact { position: absolute; left: 425px; top: 65px; color: var(--silver); }
  .contact__name { font-size: 34px; font-weight: 500; line-height: 1.1; }
  .contact__role { font-size: 17px; color: var(--grey); margin-bottom: 22px; }
  .contact__address { font-size: 17px; line-height: 24px; margin-bottom: 16px; }
  .contact__line { display: flex; align-items: center; gap: 10px; font-size: 17px; line-height: 28px; }
  .contact__line svg { width: 13px; height: 13px; flex: none; }
</style>
</head>
<body>
  <section class="card card--back">
    <div class="brand-block">
      <div class="brand">
        <span class="brand__dot"></span>
        <span class="brand__name">Birch Pin Links</span>
      </div>
      <p class="slogan">Par Is Good. Birdie Is Better. Be Better.</p>
    </div>
    <div class="pitch">
      <p class="pitch__title">Elevator Pitch</p>
      <p>We work with serious golfers and those that want to be serious golfers…</p>
      <p>to make you better, faster, at all phases of the game…</p>
      <p>We use the same state-of-the-art technology as professional golfers…</p>
      <p>which produces data sets that shows your improvement in real time.</p>
      <p>Our facility is available 24/7 to our members, which allows you to improve on your time.</p>
    </div>
  </section>

  <section class="card card--front">
    <div class="brand-block">
      <div class="brand">
        <span class="brand__dot"></span>
        <span class="brand__name">Birch Pin Links</span>
      </div>
      <p class="slogan">Par Is Good. Birdie Is Better. Be Better.</p>
    </div>
    <div class="divider"></div>
    <div class="contact">
      <p class="contact__name">Daniel Reyes</p>
      <p class="contact__role">Director</p>
      <p class="contact__address">418 W. Alder Rd. Unit B3<br>Fairbrook, OH 45099</p>
      <p class="contact__line">
        <svg viewBox="0 0 16 16" aria-hidden="true"><path fill="#919191" d="M3.6 1.2l2.2 2.6-1.3 1.6c.9 2 2.6 3.7 4.6 4.6l1.6-1.3 2.6 2.2-1.2 2.4C7 13 3 9 1.2 3.6z"/></svg>
        555-210-3377
      </p>
      <p class="contact__line">
        <svg viewBox="0 0 16 16" aria-hidden="true"><rect x="1" y="3" width="14" height="10" fill="none" stroke="#919191" stroke-width="1.5"/><path d="M1 3.5l7 5 7-5" fill="none" stroke="#919191" stroke-width="1.5"/></svg>
        info@birchpinlinks.com
      </p>
      <p class="contact__line">
        <svg viewBox="0 0 16 16" aria-hidden="true"><circle cx="8" cy="8" r="6.5" fill="none" stroke="#919191" stroke-width="1.4"/><ellipse cx="8" cy="8" rx="2.8" ry="6.5" fill="none" stroke="#919191" stroke-width="1.2"/><path d="M1.5 8h13" stroke="#919191" stroke-width="1.2"/></svg>
        www.birchpinlinks.com
      </p>
    </div>
  </section>
</body>
</html>
```